professional business card design for technology company

We are a small technology consulting firm, specialising in consulting based around Cloud and Managed services. Our colour scheme is yellow, blue and white, as you can see in the logos. Although we are based in melbourne australia, due to the nature of our work, our clients can be located anywhere. We are looking for a clean, professional, positive look - similar to our company logo

Target Market(s)

small business

Industry/Entity Type

Business

Contact Information for Business Card

eye catching, designed to incorporate some level of raised printing. Must contain website address, phone number, name and job title

Requirements
Must have
• Logo (attached) - use of the same colour scheme

```html
<!DOCTYPE html>
<html lang="en">
<head>
<meta charset="utf-8">
<title>Nubera Business Card</title>
<link href="https://fonts.googleapis.com/css2?family=Raleway:ital,wght@0,400;0,500;0,600;0,800;1,400;1,500&display=swap" rel="stylesheet">
<style>
  :root{
    --bg:#e4e4e4;
    --card:#f1f1f1;
    --ink:#1c1c1c;
    --band:#222222;
    --band-light:#2e2e2e;
    --blue:#1e9ad6;
    --yellow:#f2d21b;
    --grey:#5a5a5a;
    --text:#333333;
  }
  *{margin:0;padding:0;box-sizing:border-box}
  html,body{width:1200px;height:960px;overflow:hidden;background:var(--bg)}
  body{position:relative;font-family:"Raleway",sans-serif;color:var(--text)}
  .card{
    position:absolute;left:220px;width:760px;height:434px;
    background:var(--card);overflow:hidden;
    box-shadow:0 6px 18px rgba(0,0,0,.15);
  }
  .card--front{top:30px}
  .card--back{top:496px}

  /* front */
  .front-band{position:absolute;left:0;top:150px;width:100%;height:104px;background:var(--band)}
  .front-band__mark{position:absolute;left:0;top:150px;width:330px;height:104px}
  .front-brand{
    position:absolute;left:350px;top:152px;height:100px;display:flex;align-items:center;
    font-weight:800;font-size:78px;letter-spacing:-1px;color:#ffffff;line-height:1;
  }
  .front-brand__dot{
    position:absolute;left:120px;top:174px;width:56px;height:56px;border-radius:50%;
    background:var(--yellow);
  }
  .front-web{
    position:absolute;left:0;right:0;top:352px;display:flex;justify-content:center;align-items:center;gap:14px;
    font-size:17px;letter-spacing:2px;color:var(--text);
  }
  .front-web svg{width:14px;height:14px}

  /* back */
  .name-tag{position:absolute;left:80px;top:0;width:330px;height:84px}
  .name-tag__shape{position:absolute;inset:0}
  .name-tag__icon{position:absolute;left:18px;top:14px;width:44px;height:44px}
  .name-tag__name{
    position:absolute;left:74px;top:14px;font-size:23px;font-weight:500;letter-spacing:.5px;
    color:#8c8c8c;text-transform:uppercase;white-space:nowrap;
  }
  .name-tag__name span{color:var(--blue)}
  .name-tag__title{position:absolute;left:76px;top:44px;font-size:15px;font-style:italic;color:#d8d8d8}
  .contact-list{position:absolute;left:60px;top:150px;list-style:none}
  .contact-list li{display:flex;align-items:center;gap:14px;height:40px;font-size:16px;color:var(--ink)}
  .contact-list svg{width:32px;height:32px}
  .back-brand{
    position:absolute;left:390px;top:150px;display:flex;align-items:center;gap:16px;
  }
  .back-brand__dot{width:58px;height:58px;border-radius:50%;background:var(--yellow);flex:none}
  .back-brand__name{font-weight:800;font-size:64px;letter-spacing:-1px;color:var(--grey);line-height:1;white-space:nowrap}
</style>
</head>
<body>

<section class="card card--front" aria-label="Card front">
  <div class="front-band"></div>
  <svg class="front-band__mark" viewBox="0 0 330 104" preserveAspectRatio="none" aria-hidden="true">
    <polygon points="0,0 300,0 330,52 300,104 0,104" fill="var(--band-light)"/>
  </svg>
  <div class="front-brand__dot"></div>
  <div class="front-brand">Nubera</div>
  <div class="front-web">
    <svg viewBox="0 0 14 14" aria-hidden="true"><circle cx="7" cy="7" r="7" fill="var(--blue)"/><path d="M2 7h10M7 1c2.5 3 2.5 9 0 12M7 1c-2.5 3-2.5 9 0 12" stroke="#fff" stroke-width="1" fill="none"/></svg>
    <span>www.nubera.com</span>
  </div>
</section>

<section class="card card--back" aria-label="Card back">
  <div class="name-tag">
    <svg class="name-tag__shape" viewBox="0 0 330 84" preserveAspectRatio="none" aria-hidden="true">
      <polygon points="0,0 330,0 330,50 296,84 0,84" fill="var(--ink)"/>
    </svg>
    <svg class="name-tag__icon" viewBox="0 0 44 44" aria-hidden="true">
      <circle cx="22" cy="22" r="19" fill="none" stroke="var(--blue)" stroke-width="3"/>
      <circle cx="22" cy="17" r="6" fill="#e6e6e6"/>
      <path d="M11 33c1-7 21-7 22 0z" fill="#e6e6e6"/>
    </svg>
    <div class="name-tag__name">Daniel <span>Harlow</span></div>
    <div class="name-tag__title">Sales Director</div>
  </div>

  <ul class="contact-list">
    <li>
      <svg viewBox="0 0 32 32" aria-hidden="true"><circle cx="16" cy="16" r="14" fill="none" stroke="#777" stroke-width="1.6"/><path d="M11 10c0 7 4 11 11 12l1.5-3-3-1.5-1.5 1.5c-2-1-3.5-2.5-4.5-4.5l1.5-1.5L14.5 10z" fill="var(--blue)"/></svg>
      <span>555-014-2280</span>
    </li>
    <li>
      <svg viewBox="0 0 32 32" aria-hidden="true"><circle cx="16" cy="16" r="14" fill="none" stroke="#777" stroke-width="1.6"/><circle cx="16" cy="16" r="7" fill="var(--blue)"/><path d="M9 16h14M16 9c3 3 3 11 0 14M16 9c-3 3-3 11 0 14" stroke="#fff" stroke-width="1" fill="none"/></svg>
      <span>www.nubera.com</span>
    </li>
    <li>
      <svg viewBox="0 0 32 32" aria-hidden="true"><circle cx="16" cy="16" r="14" fill="none" stroke="#777" stroke-width="1.6"/><rect x="9" y="11" width="14" height="10" fill="var(--blue)"/><path d="M9 11l7 6 7-6" stroke="#fff" stroke-width="1.2" fill="none"/></svg>
      <span>hello@nubera.com</span>
    </li>
  </ul>

  <div class="back-brand">
    <div class="back-brand__dot"></div>
    <div class="back-brand__name">Nubera</div>
  </div>
</section>

</body>
</html>
```